Medical Practice and Business Coaching Website Design

I need a professional website designed for a medical business, TQP Medical.
The website will be hosted on Vorluna (similar design functionality as ZEPT).

About the website:
Pages for the website:
- Home page (a brief overview of the company with a section for "Ultrasound Clinics" and "Coaching and Courses" that link to these pages with all the info and packages for these sections)
- About Us (section for company info and info about Delphine Ashcombe, founder and business coach)
- Ultrasound Clinics (all the info about ultrasound, our packages, links to book, gallery of 3D/4D images, FAQs, social media links)
- Coaching and Courses (All of our coaching package info, course info with a waiting list sign up, section for free business download resources, social media links, blog posts)
- Contact Us (info for our harrowgate ultrasound location and bookings with a map, contact form, email and phone details)

Pages that are also needed but not visible in the top menu:
- Blog Page
- Waiting List Page x2 (Marlowe pop-up 3D clinic, Online Course)
- Thanks for subscribing page

We have a company logo and a logo for both the ultrasound clinics and the Coaching sides of the business. They are attached as well as the HEX codes for the branding colours. Ideally the company areas of the site will be in the blue, purple and teal colours. The ultrasound clinics page will be mostly in the purple with the "clinics" logo featuring on the page.
The courses and coaching page will be dominant in the blue branding colours with accents of purple and teal. The courses logo will be somewhere on the page too.

About our company:
Our company has 2 separate businesses which will have their own pages on the website.
We have a medical imaging business which specialises in ultrasound. We have 3 locations/services:
- Harrowgate Ultrasound: open Fridays and the occasional saturday. Our main focus and where the focus on the clinical page needs to be.
- East Corrimbal Ultrasound: Currently closed, no re-opening date and unlikely to reopen.
- Pop-up clinics: most commonly occur in Marlowe. occasionally in Parkes. Dates for next pop-up will be announced in the future.

Our Harrowgate practice offers both diagnostic ultrasound (referral from doctor) for all areas of the body and 3d/4d pregnancy ultrasounds for entertainment purposes.
The content for the ultrasound clinics part of the website can be found on the current harrowgate ultrasound website: harrowgateultrasound.com.au
This website will be replaced by the new company site. All of the info on this site will end up on the clinics page of the new company website.

The second part of the company is a coaching and courses service for medical professionals who want to start or grow their business.
We currently have coaching packages for 1-on-1 online advice and guidance.

Coaching: all take place on Zoom and can be recorded for them to watch again after. Notes, documents and links that are discussed are provided after session

- FREE 15 minute session: discuss current business or business idea, if and how I can help and potential things they can do. One per client

- Single Coaching Session - 1hr with Delphine

- Silver coaching package: 1 x 1hr Coaching Call with Delphine
Unlimited Email with Delphine for 1 month
Access to our Private Facebook Group to network with other medical professionals and business owners

- Silver Coaching Package With Social Media Management:
As above with 1 month Social Media Management (15 posts, Facebook and Instagram)

- Gold coaching package: 2 x 1hr Coaching Calls with Delphine
Access to our Private Facebook

- Gold Coaching Package With Social Media Management:

- Business Sidekick Package: Unlimited Coaching Calls
Unlimited SMS
Unlimited Emails
Social Media Management (Facebook and Instagram, 1 post per day) Valued at over $700
Business Masterclass (something different each month...social media, medicare, website, branding, live events, etc)

Enrollment for our first course opens in May and clients can join the waitlist in the meantime.
Course is aimed at medical professionals who want to grow their patient numbers and create an online presence for their business.
Ideal for: small practices where the owner does everything, not necessarily familiar with marketing/social media/websites, goes to the very basics and steps through everything in getting a logo, branding, website, building social media pages, creating content.

Course name to come but it will be something like "helpful marketing in healthcare" or "the business of healthcare"

We will also have a blog on the website and a podcast (in the future).

I would like a testimonial on at least the clinics page and the coaching page. Here is one for each but I have more if need be:
Coaching: "I knew I wanted to start my own business but I had no idea where to begin. It would have been easy to abort my dreams of starting my own business had it not been for the direction and unwavering support of Delphine from TQP medical. Delphine dissected the process into manageable bit sized pieces for me and worked tirelessly behind the scenes ensuring everything was on track. Her friendly, warm and approachable manner
equated to more than her just being my business coach, she has now become a friend.
Thank you!!"

Ultrasound testimonial: "Amazing service! Best ultrasound experience I’ve had. Super friendly and informative staff. Great technology. If I didn’t live so far away I’d go to Harrowgate for all my ultrasounds!"

I would also like a section for a welcome video (yet to be recorded) on the home page, ultrasound clinics page and coaching/courses page.

I've attached the company logo and the sub-logos in different formats. There is also a head shot of Delphine for the about us page, an image of Delphine with a coaching client for the coaching page and multiple 3D ultrasound images for the gallery on the clinics page.

Target Market(s)

Mostly targeted at medical professionals. Pregnant women and anyone needing an ultrasound are the targets for the clinics page

Industry/Entity Type

Healthcare

Number of Pages Required

5+ page

Colors
0054AA
0677BA
7BADD7
CADEEF
E8F1F8
0094D4
00A9DD
6FCCEA
C7EBF8
E9F6FB
00AB8E
00BBA5
67D7C9
C6EFE9
E9F9F6
A7469A
B969AE
D3A5CF
EDDBEB
F8F0F9
6B429C
8869AF
B7A5CE
E3DAEB
F3F0F8

```html
<!DOCTYPE html>
<html lang="en">
<head>
<meta charset="utf-8">
<title>TQP Medical</title>
<link rel="stylesheet" href="https://fonts.googleapis.com/css2?family=Bodoni+Moda:wght@600;700&family=Libre+Baskerville:ital,wght@0,400;0,700;1,400&family=Poppins:wght@500&display=swap">
<style>
:root{
  --blue-deep:#0054AA;
  --blue:#0677BA;
  --sky:#0094D4;
  --sky-light:#C7EBF8;
  --teal:#00AB8E;
  --teal-bright:#00BBA5;
  --magenta:#A7469A;
  --magenta-soft:#D3A5CF;
  --purple:#6B429C;
  --purple-mid:#8869AF;
  --navy:#27307f;
  --ink:#222222;
  --grey:#7a7a7a;
  --grey-light:#f5f5f5;
  --line:#d8d8d8;
  --white:#ffffff;
  --black:#0a0a0a;
  --heading:"Bodoni Moda", "Libre Baskerville", serif;
  --body:"Libre Baskerville", Georgia, serif;
  --ui:"Poppins", Arial, sans-serif;
}
*{margin:0;padding:0;box-sizing:border-box}
html,body{width:1200px;height:5046px;overflow:hidden}
body{position:relative;background:var(--white);font-family:var(--body);color:var(--ink)}
.abs{position:absolute}
.heading{font-family:var(--heading);font-weight:700;text-transform:uppercase;line-height:1.3}
.btn{position:absolute;display:flex;align-items:center;justify-content:center;border-radius:40px;color:var(--white);font-family:var(--body);font-weight:700;text-transform:uppercase;letter-spacing:.5px}

/* Top bar & nav */
.topbar{left:0;top:0;width:1200px;height:58px;background:linear-gradient(90deg,var(--purple) 0%,var(--blue) 35%,var(--teal-bright) 60%,var(--purple-mid) 100%)}
.social-row{display:flex;gap:10px;align-items:center}
.social-dot{width:18px;height:18px;border-radius:50%;background:var(--white)}
.topbar .social-row{position:absolute;left:678px;top:20px}
.phone{position:absolute;left:870px;top:16px;color:var(--white);font-size:17px;display:flex;align-items:center;gap:10px}
.header{left:0;top:58px;width:1200px;height:126px;background:var(--white)}
.brand-badge{left:155px;top:10px;width:112px;height:112px;border-radius:50%;background:var(--white);box-shadow:0 2px 6px rgba(0,0,0,.08)}
.brand-badge .mark{position:absolute;left:22px;top:14px;width:68px;height:68px;border-radius:50%;background:var(--teal)}
.brand-name{left:130px;top:118px;width:160px;text-align:center;font-family:var(--heading);font-weight:600;color:var(--purple);font-size:19px;line-height:1.05;letter-spacing:2px}
.nav{left:0;top:113px;width:1200px;height:30px}
.nav a{position:absolute;font-size:18px;color:var(--ink);text-decoration:none}

/* Hero */
.hero-title{left:0;top:385px;width:1200px;text-align:center;color:var(--white);font-size:58px}
.hero-sub{left:0;top:470px;width:1200px;text-align:center;color:var(--white);font-family:var(--heading);font-weight:700;font-size:26px;line-height:35px}
.hero-btn{left:497px;top:573px;width:203px;height:63px;font-size:19px;background:linear-gradient(90deg,var(--purple) 0%,var(--blue) 100%)}

/* Welcome */
.welcome-title{left:681px;top:918px;font-size:33px;color:var(--purple)}
.welcome-lead{left:681px;top:1022px;width:430px;font-size:24px;line-height:31px}
.welcome-text{left:681px;top:1104px;width:420px;font-size:15.5px;line-height:22.5px;color:var(--grey)}
.divider{left:0;top:1402px;width:1200px;height:2px;background:#eeeeee}

/* Feature sections */
.feature-title{font-size:33px;line-height:43px}
.feature-text{font-size:15px;line-height:18px;color:#333}
.clinics-title{left:247px;top:1560px;color:var(--magenta)}
.clinics-text{left:247px;top:1664px;width:330px}
.clinics-btn{left:247px;top:1871px;width:146px;height:55px;font-size:15px;background:linear-gradient(90deg,var(--magenta),var(--purple))}
.coaching-title{left:661px;top:2791px;color:var(--blue-deep)}
.coaching-text{left:661px;top:2895px;width:330px}
.coaching-btn{left:661px;top:3102px;width:147px;height:53px;font-size:15px;background:linear-gradient(90deg,var(--blue-deep),var(--sky))}

/* Testimonials */
.testimonials{left:0;top:2071px;width:1200px;height:546px;background:var(--grey-light)}
.section-title{left:0;width:1200px;text-align:center}
.testimonials .section-title{top:94px;font-size:33px;color:var(--purple)}
.quote{position:absolute;width:250px}
.quote p{font-style:italic;font-size:12.5px;line-height:18px;color:var(--grey)}
.quote .name{margin-top:18px;font-size:13px;font-weight:700;color:var(--teal);font-style:normal}
.quote .city{font-size:12px;color:var(--grey);font-style:normal;line-height:18px}
.quote-mark{position:absolute;font-family:var(--heading);font-size:56px;line-height:1;color:#cfcfcf}
.avatar{position:absolute;width:128px;height:128px;border-radius:50%;padding:6px}
.avatar-inner{width:100%;height:100%;border-radius:50%;background:linear-gradient(160deg,#d9d9d9,#9a8a80)}
.pager{position:absolute;left:528px;top:463px;display:flex;gap:4px}
.pager span{width:14px;height:14px;border-radius:50%;background:#dcdcdc}
.pager span.active{background:linear-gradient(90deg,var(--purple),var(--blue))}

/* Blog */
.blog{left:0;top:3282px;width:1200px;height:782px;background:var(--grey-light)}
.blog .section-title{top:136px;font-size:42px;color:var(--navy)}
.blog .section-title span{color:var(--blue)}
.post{position:absolute;top:236px;width:290px;text-align:center}
.post-ring{width:262px;height:262px;margin:0 auto;border-radius:50%;border:5px solid;padding:8px}
.post-photo{width:100%;height:100%;border-radius:50%}
.post h3{margin-top:42px;font-size:14.5px;line-height:20px;text-transform:uppercase;font-weight:700}
.post p{margin-top:8px;font-size:14px;line-height:19px;color:var(--grey)}
.post .date{margin-top:10px;font-family:var(--ui);font-size:12px;color:var(--purple);display:flex;justify-content:center;align-items:center;gap:5px}

/* Contact */
.contact-title{top:4166px;font-size:42px;color:var(--navy)}
.field{position:absolute;font-size:16px;color:#555;border-bottom:1px solid var(--line);padding-bottom:10px}
.submit-btn{left:544px;top:4495px;width:110px;height:40px;font-size:12px;background:linear-gradient(180deg,var(--blue),var(--navy))}

/* Footer */
.footer-band{left:0;top:4638px;width:1200px;height:16px;background:linear-gradient(90deg,var(--purple),var(--navy))}
.footer{left:0;top:4654px;width:1200px;height:392px;background:var(--black);color:var(--white)}
.footer-mark{position:absolute;left:156px;top:66px;width:118px;height:118px;border-radius:50%;background:var(--blue)}
.footer-name{position:absolute;left:110px;top:186px;width:210px;text-align:center;font-family:var(--heading);font-weight:600;font-size:26px;line-height:26px;letter-spacing:3px}
.footer-links{position:absolute;left:356px;top:88px;list-style:none;font-size:14px;line-height:29px}
.footer-col{position:absolute;left:589px;top:88px;font-size:14px;line-height:29px}
.footer-col ul{list-style:none;color:#9a9a9a;font-size:12.5px;line-height:24px;margin-left:8px}
.footer-col li::before{content:"";display:inline-block;width:5px;height:5px;border-radius:50%;background:var(--purple-mid);margin-right:9px;vertical-align:middle}
.newsletter{position:absolute;left:826px;top:84px;width:224px}
.newsletter h4{font-size:18px;font-weight:400}
.newsletter .email{margin-top:18px;font-size:13px;border-bottom:2px solid var(--white);padding-bottom:4px}
.signup-btn{left:0;top:82px;width:110px;height:39px;font-size:13px;background:linear-gradient(90deg,var(--sky),var(--blue))}
.footer-rule{position:absolute;left:147px;top:284px;width:910px;height:1px;background:#444}
.footer .social-row{position:absolute;left:168px;top:332px}
.copyright{position:absolute;right:153px;top:328px;font-size:12px}
</style>
</head>
<body>

<!-- Header -->
<div class="abs topbar">
  <div class="social-row" aria-label="Social media links">
    <span class="social-dot"></span><span class="social-dot"></span><span class="social-dot"></span><span class="social-dot"></span><span class="social-dot"></span>
  </div>
  <div class="phone">
    <svg width="16" height="16" viewBox="0 0 24 24" aria-hidden="true"><path fill="#fff" d="M6.6 10.8a15.1 15.1 0 0 0 6.6 6.6l2.2-2.2a1 1 0 0 1 1-.25 11.4 11.4 0 0 0 3.6.57 1 1 0 0 1 1 1V20a1 1 0 0 1-1 1A17 17 0 0 1 3 4a1 1 0 0 1 1-1h3.5a1 1 0 0 1 1 1c0 1.250.2 2.45.57 3.57a1 1 0 0 1-.25 1z"/></svg>
    Call Us: 555 014 2271
  </div>
</div>
<div class="abs header"></div>
<div class="abs brand-badge"><span class="mark"></span></div>
<div class="abs brand-name">TQP<br>MEDICAL</div>
<nav class="abs nav">
  <a style="left:338px">Home</a>
  <a style="left:434px">About Us</a>
  <a style="left:557px">Ultrasound Clinics</a>
  <a style="left:757px">Coaching and Courses</a>
  <a style="left:992px">Contact Us</a>
</nav>

<!-- Hero -->
<svg class="abs" style="left:0;top:184px" width="1200" height="630" role="img" aria-label="Photo of a sonographer performing a pregnancy ultrasound scan">
  <defs>
    <linearGradient id="heroFill" x1="0" y1="0" x2="1" y2="1">
      <stop offset="0" stop-color="#5d5a59"/>
      <stop offset=".5" stop-color="#8c8988"/>
      <stop offset="1" stop-color="#b9b4b2"/>
    </linearGradient>
  </defs>
  <path d="M0 0H1200V516Q600 744 0 516Z" fill="url(#heroFill)"/>
</svg>
<h1 class="abs heading hero-title">TQP Medical</h1>
<p class="abs hero-sub">LOREM IPSUM DOLOR SIT AMET, CONSE CTE TUR<br>ADIPISCIN LAB ORE ET DOLORE MAGNA</p>
<a class="btn hero-btn">Read More</a>

<!-- Welcome -->
<div class="abs" style="left:100px;top:1102px;width:282px;height:213px;background:linear-gradient(135deg,rgba(0,171,142,.25),rgba(107,66,156,.35))" role="img" aria-label="Dotted accent pattern"></div>
<div class="abs" style="left:147px;top:930px;width:473px;height:346px;background:linear-gradient(135deg,#c9dbe8,#7fa6c4 60%,#e2e9ef)" role="img" aria-label="Welcome video still: hand holding an ultrasound probe"></div>
<svg class="abs" style="left:326px;top:1056px" width="92" height="92" aria-label="Play video">
  <defs><linearGradient id="playFill" x1="0" y1="0" x2="1" y2="1"><stop offset="0" stop-color="#6B429C"/><stop offset="1" stop-color="#0677BA"/></linearGradient></defs>
  <circle cx="46" cy="46" r="44" fill="none" stroke="#fff" stroke-opacity=".6" stroke-width="2"/>
  <circle cx="46" cy="46" r="38" fill="url(#playFill)"/>
  <path d="M38 30L62 46L38 62Z" fill="#fff"/>
</svg>
<h2 class="abs heading welcome-title">Welcome to<br>TQP Medical</h2>
<p class="abs welcome-lead">Lorem ipsum dolor sit ametempor incididunt utlabore magna aliua.</p>
<p class="abs welcome-text">Lorem ipsum dolor sit amet, consectetur adipisg elit, sed do eiusmod tempor incididunt ut labore et dolore magna aliqua. Quis ipsum suspendisse ultrices avida. Risus commodo viverra maecenas accumsan lacu vel facilisis. Lorem ipsum dolor sit amet, consectetur adipiscing elit, sed do eiusmod tempor incididunt ut labore et dolore magna aliqua.</p>
<div class="abs divider"></div>

<!-- Ultrasound clinics -->
<svg class="abs" style="left:0;top:1403px" width="1200" height="668">
  <defs>
    <linearGradient id="clinicsFill" x1="0" y1="0" x2="1" y2="1"><stop offset="0" stop-color="#A7469A"/><stop offset="1" stop-color="#6B429C"/></linearGradient>
  </defs>
  <path d="M722 0C800 77 860 157 780 297C690 447 680 577 700 668H1200V0Z" fill="url(#clinicsFill)"/>
  <circle cx="110" cy="560" r="150" fill="none" stroke="#EDDBEB" stroke-width="10"/>
  <circle cx="841" cy="339" r="205" fill="none" stroke="#D3A5CF" stroke-width="4"/>
  <circle cx="841" cy="339" r="190" fill="none" stroke="#fff" stroke-width="6"/>
</svg>
<div class="abs" style="left:671px;top:1572px;width:340px;height:340px;border-radius:50%;background:linear-gradient(160deg,#e9e4e2,#c96a5e 55%,#8a7f86)" role="img" aria-label="Photo of two clinic staff beside an ultrasound machine"></div>
<h2 class="abs heading feature-title clinics-title">Ultrasound<br>Clinics</h2>
<p class="abs feature-text clinics-text">Lorem ipsum dolor sit amet, consectetur adipiscing elit, sed do eiusmod tempor incididunt ut lablorore et dolore magna ali qua uis ipsum suspendisse uloreltrices avida sus commodo viverloyra maecenas accusan lacus vel facilisis. Lorem ipsum dolor sit aet, consectetur adipiscing elit, sed do eiusmod tempor incididunt ut labore et dolore magna aliquacommodo viverra maecenas accsan la cus vel facilisis.</p>
<a class="btn clinics-btn">Read More</a>

<!-- Testimonials -->
<section class="abs testimonials">
  <h2 class="abs heading section-title">Client Testimonials</h2>
  <div class="avatar" style="left:151px;top:217px;border:3px solid var(--teal)"><div class="avatar-inner" role="img" aria-label="Client portrait"></div></div>
  <span class="quote-mark" style="left:272px;top:212px">&ldquo;</span>
  <div class="quote" style="left:315px;top:223px">
    <p>Lorem ipsum dolor sit amet, consectetur adipiscing elit, sed do eiusmod tempor incididunt ut labore et dolore magna ali q uauis ipsum suspendisse ultrices gra vidaisus commodo viverra maecenas accumsan lacus vel facilisiorem ipsum dolor sit amet, consectetur</p>
    <p class="name">JHSNO SML</p>
    <p class="city">CITY NAME</p>
  </div>
  <div class="abs" style="left:599px;top:196px;width:1px;height:166px;background:#dddddd"></div>
  <div class="avatar" style="left:631px;top:217px;border:3px solid var(--purple)"><div class="avatar-inner" role="img" aria-label="Client portrait"></div></div>
  <span class="quote-mark" style="left:752px;top:212px">&ldquo;</span>
  <div class="quote" style="left:795px;top:223px">
    <p>Lorem ipsum dolor sit amet, consectetur adipiscing elit, sed do eiusmod tempor incididunt ut labore et dolore magna ali q uauis ipsum suspendisse ultrices gra vidaisus commodo viverra maecenas accumsan lacus vel facilisiorem ipsum dolor sit amet, consectetur</p>
    <p class="name">JHSNO SML</p>
    <p class="city">CITY NAME</p>
  </div>
  <div class="pager"><span class="active"></span><span></span><span></span><span></span><span></span><span></span><span></span><span></span><span></span></div>
</section>

<!-- Coaching and courses -->
<svg class="abs" style="left:0;top:2617px" width="1200" height="665">
  <defs>
    <linearGradient id="coachFill" x1="0" y1="0" x2="1" y2="1"><stop offset="0" stop-color="#0054AA"/><stop offset="1" stop-color="#0094D4"/></linearGradient>
  </defs>
  <path d="M0 0H476C420 83 400 163 430 283C470 433 480 563 474 665H0Z" fill="url(#coachFill)"/>
  <circle cx="1060" cy="560" r="150" fill="none" stroke="#E9F6FB" stroke-width="10"/>
  <circle cx="358" cy="358" r="205" fill="none" stroke="#6FCCEA" stroke-width="4"/>
  <circle cx="358" cy="358" r="190" fill="none" stroke="#fff" stroke-width="6"/>
</svg>
<div class="abs" style="left:188px;top:2805px;width:340px;height:340px;border-radius:50%;background:radial-gradient(circle at 45% 45%,#c98a55,#5a3019 65%,#0d0806)" role="img" aria-label="3D ultrasound image of a baby"></div>
<h2 class="abs heading feature-title coaching-title">Coaching<br>and Courses</h2>
<p class="abs feature-text coaching-text">Lorem ipsum dolor sit amet, consectetur adipiscing elit, sed do eiusmod tempor incididunt ut lablorore et dolore magna ali qua uis ipsum suspendisse uloreltrices avida sus commodo viverloyra maecenas accusan lacus vel facilisis. Lorem ipsum dolor sit aet, consectetur adipiscing elit, sed do eiusmod tempor incididunt ut labore et dolore magna aliquacommodo viverra maecenas accsan la cus vel facilisis.</p>
<a class="btn coaching-btn">Read More</a>

<!-- Blog -->
<section class="abs blog">
  <h2 class="abs heading section-title">Latest <span>Blog Posts</span></h2>
  <article class="post" style="left:145px">
    <div class="post-ring" style="border-color:var(--purple)"><div class="post-photo" role="img" aria-label="Photo of a smiling pregnant woman during a scan" style="background:linear-gradient(150deg,#d8d2cf,#9f918d)"></div></div>
    <h3>Lorem ipsum dolor sit am<br>cons ectetur ascing</h3>
    <p>Lorem ipsum dolor sit amet, consec tet ur adipiscing elit, sed do eiusmod tem por incididunt ut lablorvel facilisis.</p>
    <div class="date"><svg width="11" height="11" viewBox="0 0 12 12" aria-hidden="true"><rect x="1" y="2" width="10" height="9" fill="#6B429C"/><rect x="3" y="0" width="1.5" height="3" fill="#6B429C"/><rect x="7.5" y="0" width="1.5" height="3" fill="#6B429C"/></svg>March 18</div>
  </article>
  <article class="post" style="left:454px">
    <div class="post-ring" style="border-color:var(--teal)"><div class="post-photo" role="img" aria-label="Photo of an ultrasound probe on a pregnant belly" style="background:linear-gradient(150deg,#4a5a6a,#c8d6e3 55%,#e7e0da)"></div></div>
    <h3>Lorem ipsum dolor sit am<br>cons ectetur ascing</h3>
    <p>Lorem ipsum dolor sit amet, consec tet ur adipiscing elit, sed do eiusmod tem por incididunt ut lablorvel facilisis.</p>
    <div class="date" style="color:var(--teal)"><svg width="11" height="11" viewBox="0 0 12 12" aria-hidden="true"><rect x="1" y="2" width="10" height="9" fill="#00AB8E"/><rect x="3" y="0" width="1.5" height="3" fill="#00AB8E"/><rect x="7.5" y="0" width="1.5" height="3" fill="#00AB8E"/></svg>March 18</div>
  </article>
  <article class="post" style="left:775px">
    <div class="post-ring" style="border-color:var(--navy)"><div class="post-photo" role="img" aria-label="Photo of a pregnant woman holding an ultrasound print" style="background:linear-gradient(150deg,#e8ddd3,#b89a85 60%,#5c5350)"></div></div>
    <h3>Lorem ipsum dolor sit am<br>cons ectetur ascing</h3>
    <p>Lorem ipsum dolor sit amet, consec tet ur adipiscing elit, sed do eiusmod tem por incididunt ut lablorvel facilisis.</p>
    <div class="date" style="color:var(--navy)"><svg width="11" height="11" viewBox="0 0 12 12" aria-hidden="true"><rect x="1" y="2" width="10" height="9" fill="#27307f"/><rect x="3" y="0" width="1.5" height="3" fill="#27307f"/><rect x="7.5" y="0" width="1.5" height="3" fill="#27307f"/></svg>March 18</div>
  </article>
</section>

<!-- Contact -->
<h2 class="abs heading section-title contact-title">Contact Us</h2>
<div class="field" style="left:292px;top:4266px;width:301px">Name:</div>
<div class="field" style="left:618px;top:4266px;width:302px">Phone:</div>
<div class="field" style="left:292px;top:4328px;width:301px">Email:</div>
<div class="field" style="left:618px;top:4328px;width:302px">Subject:</div>
<div class="field" style="left:292px;top:4398px;width:616px;height:61px">Message:</div>
<a class="btn submit-btn">Submit</a>

<!-- Footer -->
<div class="abs footer-band"></div>
<footer class="abs footer">
  <div class="footer-mark"></div>
  <div class="footer-name">TQP<br>MEDICAL</div>
  <ul class="footer-links">
    <li>Home</li><li>About Us</li><li>Ultrasound Clinics</li><li>Coaching and Courses</li><li>Contact Us</li>
  </ul>
  <div class="footer-col">
    <div>Waiting List</div>
    <ul><li>Marlowe pop-up 3D clinic</li><li>Online Course</li></ul>
    <div>Blog page</div>
  </div>
  <div class="newsletter">
    <h4>Subscribe Newsletter</h4>
    <div class="email">Email</div>
    <a class="btn signup-btn">Sign Up</a>
  </div>
  <div class="footer-rule"></div>
  <div class="social-row" aria-label="Social media links">
    <span class="social-dot"></span><span class="social-dot"></span><span class="social-dot"></span><span class="social-dot"></span><span class="social-dot"></span>
  </div>
  <div class="copyright">Copyrights © 2022 All Rights Reserved</div>
</footer>

</body>
</html>
```